Company website for an international IT business

We require a website for our business, Korvel Solutions. The business has two primary areas: Lanterns, which includes two machine learning/deep learning based products and IT consultancy, which is the service we provide to other businesses.

We bridge cutting-edge research to market.

STYLING:
The site can be on single page or multi-page. This is fully open to suggestion. So long as the look and feel are consistent. Currently, we have no strong preference for colors, styles or layouts.
You can find the logo of our website in the attachment “Korvel-logo.png” and “Korvel-logo-landscape.png”.

CONTENT:
You can find the text of the website in “Website-Content.pdf”, which explains the services and products of our business. The format of the text is also open to suggestion - including breaking up the text into visually appealing sections.
We would also like to include suitable images on the website so that it does not appear to be a text-heavy page. We are happy to have placeholder images on stock image sites if needed. We are open to suggestions on placing of images

ATTACHMENT:

Industry/Entity Type

It Company

Coding

Coded - Design and coding required

Number of Pages Required

1 page

Colors

Designer to choose colors to be used in the design.

Requirements
Must have
• A full description of the requirement is in the attachment "Website-Content.pdf"
• The design must have HTML/CSS, and all resources relevant (images, fonts etc)
• We are
Nice to have
• We are open to suggestions on top of the requirement, please reach out and communicate.

```html
<!DOCTYPE html>
<html lang="en">
<head>
<meta charset="utf-8">
<title>Korvel Lanterns</title>
<link href="https://fonts.googleapis.com/css2?family=Dosis:wght@400;500;600;700&family=Saira+Condensed:wght@500;600;700&display=swap" rel="stylesheet">
<style>
  :root {
    --navy: #0f3d70;
    --navy-deep: #0a2f5c;
    --button: #0b3466;
    --accent: #1a86c7;
    --white: #ffffff;
    --text: #333a44;
    --heading: #2f3540;
    --band: #e8eaee;
    --panel-dark: #333333;
  }
  * { margin: 0; padding: 0; box-sizing: border-box; }
  html, body { width: 1200px; height: 1174px; overflow: hidden; background: var(--white); }
  body { position: relative; font-family: "Dosis", sans-serif; color: var(--text); }

  .hero {
    position: absolute; left: 0; top: 0; width: 1200px; height: 628px;
    background: radial-gradient(ellipse at 45% 55%, #1d5a94 0%, var(--navy) 50%, var(--navy-deep) 100%);
  }
  .brand { position: absolute; left: 120px; top: 32px; width: 110px; text-align: center; }
  .brand-mark { display: block; margin: 0 auto; }
  .brand-name { display: block; margin-top: 4px; font-family: "Dosis", sans-serif; font-weight: 700;
    font-size: 22px; letter-spacing: 2px; color: var(--white); }

  .social-top { position: absolute; top: 31px; left: 899px; display: flex; gap: 13px; }
  .social-dot { width: 26px; height: 26px; border-radius: 50%; background: var(--white); display: block; }

  .main-nav { position: absolute; top: 74px; left: 648px; font-family: "Saira Condensed", sans-serif;
    font-weight: 600; font-size: 14px; color: var(--white); text-transform: uppercase; }
  .main-nav a { position: absolute; white-space: nowrap; color: inherit; text-decoration: none; }

  .hero-title { position: absolute; left: 120px; width: 600px; top: 222px; text-align: center;
    font-family: "Saira Condensed", sans-serif; font-weight: 700; font-size: 60px; color: var(--white);
    letter-spacing: 0.5px; line-height: 1.2; }
  .hero-lead { position: absolute; left: 120px; width: 600px; top: 340px; text-align: center;
    font-family: "Saira Condensed", sans-serif; font-weight: 500; font-size: 20px; line-height: 32px;
    color: var(--white); text-transform: uppercase; }

  .product-card { position: absolute; left: 802px; top: 184px; width: 278px; height: 382px;
    background: var(--white); border-radius: 6px; }
  .product-media { position: absolute; left: 28px; top: 15px; width: 222px; height: 195px;
    border-radius: 6px; background: radial-gradient(circle at 50% 55%, #6b6e72 0%, #3a3b3d 45%, #262626 100%); }
  .media-arrow { position: absolute; top: 87px; width: 30px; height: 30px; border-radius: 50%;
    background: rgba(90,90,90,0.75); }
  .media-arrow.prev { left: 0; } .media-arrow.next { right: 0; }
  .media-arrow svg { position: absolute; left: 8px; top: 7px; }
  .dots { position: absolute; display: flex; gap: 7px; }
  .dots span { width: 11px; height: 11px; border: 1.5px solid var(--white); border-radius: 50%; position: relative; }
  .dots span.active::after { content: ""; position: absolute; left: 2.5px; top: 2.5px; width: 3px; height: 3px;
    border-radius: 50%; background: var(--white); }
  .product-media .dots { left: 14px; top: 169px; }

  .share-row { position: absolute; left: 28px; top: 228px; display: flex; align-items: center; gap: 16px; }
  .share-title { font-size: 25px; font-weight: 500; color: var(--navy); }
  .social-share { position: absolute; left: 61px; top: 272px; display: flex; gap: 14px; }
  .social-share .social-dot { width: 25px; height: 25px; background: var(--navy); }
  .buy-button { position: absolute; left: 32px; top: 314px; width: 214px; height: 52px; border-radius: 6px;
    background: var(--button); color: var(--white); font-size: 19px; font-weight: 500;
    display: flex; align-items: center; justify-content: center; }

  .band { position: absolute; left: 0; width: 1200px; background: var(--band); }
  .band.top { top: 628px; height: 24px; }
  .band.bottom { top: 1154px; height: 20px; }

  .welcome { position: absolute; top: 670px; left: 0; width: 1258px; text-align: center;
    font-size: 24px; font-weight: 400; color: var(--heading); }
  .welcome strong { color: var(--navy-deep); font-weight: 600; }

  .about h3, .different h3 { font-size: 18px; font-weight: 600; color: var(--heading); line-height: 1; }
  .about { position: absolute; left: 134px; top: 722px; width: 470px; }
  .about p { margin-top: 14px; font-size: 14px; line-height: 24px; color: var(--text); }
  .different { position: absolute; left: 832px; top: 722px; }
  .different ul { list-style: none; margin-top: 10px; }
  .different li { display: flex; align-items: center; gap: 8px; height: 28px; font-size: 15px; font-weight: 500; color: var(--heading); }

  .testimonials-title { position: absolute; top: 902px; left: 0; width: 1200px; text-align: center;
    font-size: 19px; color: var(--heading); }
  .testimonial { position: absolute; left: 136px; top: 950px; width: 928px; height: 160px;
    background: var(--panel-dark); border-radius: 6px; }
  .client-photo { position: absolute; left: 17px; top: 24px; width: 99px; height: 79px;
    background: linear-gradient(135deg, #b8aaa0 0%, #8a7566 50%, #5e4b3f 100%); }
  .testimonial p { position: absolute; left: 139px; top: 20px; width: 760px; font-size: 10.5px;
    line-height: 24px; color: var(--white); }
  .testimonial .dots { left: 442px; top: 126px; gap: 5px; }
</style>
</head>
<body>
  <header class="hero">
    <div class="brand">
      <svg class="brand-mark" width="76" height="76" viewBox="0 0 76 76" aria-hidden="true">
        <circle cx="38" cy="38" r="38" fill="var(--accent)"/>
      </svg>
      <span class="brand-name">KORVEL</span>
    </div>

    <div class="social-top" aria-label="Social links">
      <span class="social-dot"></span><span class="social-dot"></span><span class="social-dot"></span>
      <span class="social-dot"></span><span class="social-dot"></span>
    </div>

    <nav class="main-nav">
      <a style="left:0">Home</a>
      <a style="left:74px">Products</a>
      <a style="left:172px">Consultancy</a>
      <a style="left:290px">About</a>
      <a style="left:367px">Contact Us</a>
    </nav>

    <h1 class="hero-title">KORVEL LANTERNS</h1>
    <p class="hero-lead">Korvel Lanterns has developed two cutting edge<br>products using machine learning and deeplearning.</p>

    <aside class="product-card">
      <div class="product-media" role="img" aria-label="Product photo: round dark in-car safety device with glowing ring">
        <span class="media-arrow prev"><svg width="14" height="16" viewBox="0 0 14 16"><path d="M10 2 L4 8 L10 14" stroke="#222" stroke-width="3" fill="none"/></svg></span>
        <span class="media-arrow next"><svg width="14" height="16" viewBox="0 0 14 16"><path d="M4 2 L10 8 L4 14" stroke="#222" stroke-width="3" fill="none"/></svg></span>
        <div class="dots"><span class="active"></span><span></span><span></span></div>
      </div>
      <div class="share-row">
        <svg width="20" height="22" viewBox="0 0 20 22" aria-hidden="true">
          <line x1="5" y1="11" x2="15" y2="4" stroke="var(--navy)" stroke-width="2"/>
          <line x1="5" y1="11" x2="15" y2="18" stroke="var(--navy)" stroke-width="2"/>
          <circle cx="5" cy="11" r="4" fill="var(--navy)"/><circle cx="15" cy="4" r="3.5" fill="var(--navy)"/>
          <circle cx="15" cy="18" r="3.5" fill="var(--navy)"/>
        </svg>
        <span class="share-title">Share This Product</span>
      </div>
      <div class="social-share" aria-label="Share links">
        <span class="social-dot"></span><span class="social-dot"></span><span class="social-dot"></span>
        <span class="social-dot"></span><span class="social-dot"></span>
      </div>
      <a class="buy-button">Buy Now</a>
    </aside>
  </header>

  <div class="band top"></div>

  <h2 class="welcome">Welcome to <strong>Korvel Lanterns</strong></h2>

  <section class="about">
    <h3>What is Korvel</h3>
    <p>Korvel Solutions is an IT consultancy firm with a difference<br>
    We can provide IT expertise for your business at any stage - from initial idea to live systems<br>
    systems focus on external factors such as speed, distance to the vehicle ahead, keeping within road</p>
  </section>

  <section class="different">
    <h3>How are we different</h3>
    <ul>
      <li><svg width="20" height="20" viewBox="0 0 20 20" aria-hidden="true"><circle cx="10" cy="10" r="9" fill="none" stroke="var(--navy)" stroke-width="1.5"/><path d="M5.5 10.5 L8.8 13.5 L14.5 6.5" fill="none" stroke="var(--navy)" stroke-width="1.6"/></svg>Project Point Person</li>
      <li><svg width="20" height="20" viewBox="0 0 20 20" aria-hidden="true"><circle cx="10" cy="10" r="9" fill="none" stroke="var(--navy)" stroke-width="1.5"/><path d="M5.5 10.5 L8.8 13.5 L14.5 6.5" fill="none" stroke="var(--navy)" stroke-width="1.6"/></svg>Responsible and accountable</li>
      <li><svg width="20" height="20" viewBox="0 0 20 20" aria-hidden="true"><circle cx="10" cy="10" r="9" fill="none" stroke="var(--navy)" stroke-width="1.5"/><path d="M5.5 10.5 L8.8 13.5 L14.5 6.5" fill="none" stroke="var(--navy)" stroke-width="1.6"/></svg>for deliverables and communication</li>
    </ul>
  </section>

  <h2 class="testimonials-title">Client&nbsp; Testimonials</h2>

  <section class="testimonial">
    <div class="client-photo" role="img" aria-label="Client portrait photo"></div>
    <p>NOVA is a system for HGV/HMT drivers to make every journey safer - safer for the driver and safer to other road users.NOVA uses advanced deep learning techniques to monitor<br>
    driver behavior in real time insidehe cabin. NOVA can detect driver distraction (mobile phone usage, smoking, failure to<br>
    focused on the road ahead) and also monitor for classic signs of fatigue. Current ADAS</p>
    <div class="dots"><span class="active"></span><span></span><span></span></div>
  </section>

  <div class="band bottom"></div>
</body>
</html>
```